Business Card Design

New business card design

Target Market(s)

Residential & Commercial Property Managers

Industry/Entity Type

Plumbing Services

Contact Information for Business Card

Name - Rowan Keddle, title - Director, Phone Number - 0431 286 517, email - rowan@tbk-plumbing.com.au, Company ABN - 73 215 904 386,

Font styles to use
Sans Serif

Colors
0054AA
0677BA
7BADD7
CADEEF
E8F1F8

```html
<!DOCTYPE html>
<html lang="en">
<head>
<meta charset="utf-8">
<title>TBK Plumbing Services – Business Card</title>
<link rel="stylesheet" href="https://fonts.googleapis.com/css2?family=Montserrat:wght@400;500;700&display=swap">
<style>
  :root {
    --backdrop: #b8b7b2;
    --card-white: #ffffff;
    --card-dark: #1d232b;
    --brand-blue: #00aeef;
    --ink: #2a2e33;
    --ink-soft: #6b7078;
    --on-dark: #ffffff;
  }
  * { box-sizing: border-box; margin: 0; padding: 0; }
  html, body { width: 1200px; height: 857px; overflow: hidden; }
  body {
    background: var(--backdrop);
    font-family: "Montserrat", sans-serif;
    position: relative;
  }
  .card {
    position: absolute;
    top: 285px;
    width: 500px;
    height: 286px;
    border-bottom: 4px solid var(--brand-blue);
    box-shadow: 0 14px 30px rgba(0,0,0,0.22);
  }
  .card--front { left: 70px; background: var(--card-white); }
  .card--back { left: 630px; background: var(--card-dark); }

  .wordmark {
    position: absolute;
    font-weight: 500;
    letter-spacing: 2px;
    line-height: 1;
  }
  .tagline {
    position: absolute;
    font-size: 7px;
    letter-spacing: 6px;
    text-transform: lowercase;
    white-space: nowrap;
  }
  .card--front .wordmark { left: 36px; top: 56px; font-size: 52px; color: var(--ink); }
  .card--front .tagline { left: 46px; top: 117px; color: var(--ink-soft); }

  .brand-mark {
    position: absolute;
    left: 300px;
    top: 38px;
    width: 150px;
    height: 150px;
    border-radius: 50%;
    background: var(--brand-blue);
  }

  .contact-name {
    position: absolute;
    left: 68px;
    top: 140px;
    font-size: 17px;
    line-height: 20px;
    font-weight: 700;
    color: var(--brand-blue);
    letter-spacing: 0.5px;
  }
  .contact-title {
    position: absolute;
    left: 68px;
    top: 162px;
    font-size: 12.5px;
    line-height: 16px;
    color: var(--ink);
  }
  .contact-list {
    position: absolute;
    left: 68px;
    top: 188px;
    list-style: none;
  }
  .contact-list li {
    display: flex;
    align-items: center;
    gap: 8px;
    font-size: 12px;
    color: var(--ink);
    height: 19px;
    white-space: nowrap;
  }
  .contact-list svg { width: 11px; height: 11px; flex: none; }

  .card--back .wordmark {
    left: 0; right: 0; top: 100px;
    text-align: center;
    font-size: 58px;
    color: var(--on-dark);
  }
  .card--back .tagline {
    left: 0; right: 0; top: 170px;
    text-align: center;
    color: var(--on-dark);
  }
</style>
</head>
<body>
  <section class="card card--front">
    <div class="wordmark">tbk</div>
    <div class="tagline">plumbing services</div>
    <div class="brand-mark" role="img" aria-label="Brand mark decoration"></div>

    <h1 class="contact-name">ROWAN KEDDLE</h1>
    <p class="contact-title">Director</p>
    <ul class="contact-list">
      <li>
        <svg viewBox="0 0 12 12" aria-hidden="true"><path d="M3 1 L5 3.5 L4 5 Q5 7 7 8 L8.5 7 L11 9 L9.5 11 Q4 10.5 1 3 Z" fill="var(--brand-blue)"/></svg>
        0431 286 517
      </li>
      <li>
        <svg viewBox="0 0 12 12" aria-hidden="true"><rect x="1" y="2.5" width="10" height="7" fill="var(--brand-blue)"/><path d="M1 2.5 L6 6.5 L11 2.5" stroke="#fff" stroke-width="1" fill="none"/></svg>
        rowan@tbk-plumbing.com.au
      </li>
      <li>
        <svg viewBox="0 0 12 12" aria-hidden="true"><circle cx="6" cy="6" r="5" fill="var(--brand-blue)"/><path d="M1 6 H11 M6 1 Q3 6 6 11 M6 1 Q9 6 6 11" stroke="#fff" stroke-width="0.8" fill="none"/></svg>
        tbk-plumbing.com.au
      </li>
      <li>
        <svg viewBox="0 0 12 12" aria-hidden="true"><rect x="2" y="1" width="8" height="10" fill="var(--brand-blue)"/><path d="M4 4 H8 M4 6 H8 M4 8 H7" stroke="#fff" stroke-width="0.8"/></svg>
        ABN 73 215 904 386
      </li>
    </ul>
  </section>

  <section class="card card--back">
    <div class="wordmark">tbk</div>
    <div class="tagline">plumbing services</div>
  </section>
</body>
</html>
```